Biz Card

MARKETING today is the most rapidly changing business discipline. Media options to reach customers, actual customer preferences and consumer buying decisions change by the minute . . . no, by the second. The behavioral data generated by all aspects of the business and the new technologies that put the data to work together produce the potential to generate business intelligence and guide smart resource allocation to influence purchase and retention. However, to realize this potential, marketing professionals at all levels and in all organizations must continuously improve their skills not just from on-the-job training but by learning from masters in the field. The Bright Horizon Guild is the training center that serves this professional development need.model logos:msi.orgama.orgcontentmarketinginstitute.comBook covers on MarketingMetrics, Marketing Anaytics
Industry/Entity Type
Business
Contact Information for Business Card
Roy A. YoungCEOMarketing Science Academyphone: 310-601-4755email: roy@marketingscience.comAddress:437 South Rexford DriveBeverly Hills, CA 89377
Look and feel
Each slider illustrates characteristics of the customer's brand and the style your logo design should communicate.

```html
<!DOCTYPE html>
<html lang="en">
<head>
<meta charset="utf-8">
<title>Bright Horizon Guild – Business Card</title>
<link href="https://fonts.googleapis.com/css2?family=Roboto:wght@400;500;700&display=swap" rel="stylesheet">
<style>
  :root {
    --backdrop: #a9a7a7;
    --brand-red: #8b2a26;
    --charcoal: #4a4848;
    --paper: #f6f5f5;
    --text-grey: #454545;
    --white: #ffffff;
  }
  * { margin: 0; padding: 0; box-sizing: border-box; }
  html, body { width: 1200px; height: 1200px; overflow: hidden; }
  body {
    background: var(--backdrop);
    font-family: "Roboto", Arial, sans-serif;
    position: relative;
  }
  .card {
    position: absolute;
    width: 713px;
    height: 418px;
    overflow: hidden;
  }
  .card--front {
    left: 238px; top: 118px;
    background: var(--brand-red);
    display: flex; align-items: center; justify-content: center;
  }
  .brand-name {
    font-weight: 700;
    display: flex; align-items: center; gap: 16px;
    white-space: nowrap;
  }
  .brand-name .dot {
    width: 14px; height: 14px; border-radius: 50%;
    background: currentColor; flex: none;
  }
  .card--front .brand-name { color: var(--white); font-size: 46px; }

  .card--back { left: 230px; top: 643px; background: var(--paper); }
  .card-wave { position: absolute; inset: 0; }
  .holder { position: absolute; right: 46px; top: 36px; text-align: right; color: var(--white); }
  .holder-name { font-size: 25px; font-weight: 500; }
  .holder-role { font-size: 15px; margin-top: 12px; letter-spacing: 0.5px; }
  .card--back .brand-name {
    position: absolute; left: 40px; top: 152px;
    color: var(--brand-red); font-size: 42px;
  }
  .contact { position: absolute; left: 40px; top: 280px; color: var(--text-grey); font-size: 18px; }
  .contact-row { display: flex; align-items: center; gap: 16px; height: 24px; }
  .contact-row svg { width: 18px; height: 18px; flex: none; fill: var(--brand-red); }
  .address { margin-top: 8px; font-size: 18px; }
</style>
</head>
<body>
  <section class="card card--front" aria-label="Card front">
    <div class="brand-name"><span class="dot"></span>Bright Horizon Guild</div>
  </section>

  <section class="card card--back" aria-label="Card back">
    <svg class="card-wave" viewBox="0 0 713 418" aria-hidden="true">
      <path d="M0,0 H713 V175 C650,172 600,120 500,86 C350,35 160,12 0,38 Z" fill="var(--brand-red)"/>
      <path d="M0,46 C110,10 270,14 400,72 C270,36 120,38 0,78 Z" fill="var(--charcoal)"/>
    </svg>
    <div class="holder">
      <div class="holder-name">Neil P. Barton</div>
      <div class="holder-role">CEO</div>
    </div>
    <div class="brand-name"><span class="dot"></span>Bright Horizon Guild</div>
    <div class="contact">
      <div class="contact-row">
        <svg viewBox="0 0 20 20"><path d="M3 6c0-2 3-3 7-3s7 1 7 3v2h-4V6H7v2H3z M5 9h10l2 8H3z"/></svg>
        310-555-0182
      </div>
      <div class="contact-row">
        <svg viewBox="0 0 20 20"><path d="M2 5h16v10H2z M3 6l7 5 7-5" fill="none" stroke="var(--brand-red)" stroke-width="1.8"/></svg>
        neil@brighthorizonguild.com
      </div>
      <div class="contact-row">
        <svg viewBox="0 0 20 20"><g fill="none" stroke="var(--brand-red)" stroke-width="1.5"><circle cx="10" cy="10" r="7.5"/><ellipse cx="10" cy="10" rx="3.3" ry="7.5"/><path d="M2.5 10h15M4 6h12M4 14h12"/></g></svg>
        www.brighthorizonguild.com
      </div>
      <div class="address">912 North Calloway Lane Beverly Hills, CA 89377</div>
    </div>
  </section>
</body>
</html>
```